Local fast-growing company in the service sector

We are looking for a modern business card design, which should also appear on our letterheads

Target Market(s)

Private and industrial sectors

Contact Information for Business Card

Vorname Name
Kellberger Str. 18
71586 Kellbach
Tel.: 07146-839214-0
Name@agentur-kvtl.de

Colors
9d9d9d
919191
aaaaaa

Requirements
Must have
• The logo (file) in silver

```html
<!DOCTYPE html>
<html lang="de">
<head>
<meta charset="utf-8">
<title>KVTL Visitenkarte</title>
<link href="https://fonts.googleapis.com/css2?family=Roboto+Condensed:wght@400;500&display=swap" rel="stylesheet">
<style>
  :root {
    --stage: #6b5a45;
    --card: #0b0b0b;
    --card-sheen: #2a2a2a;
    --silver: #aaaaaa;
    --silver-mid: #9d9d9d;
    --silver-dim: #919191;
    --name: #e6e6e6;
  }
  * { margin: 0; padding: 0; box-sizing: border-box; }
  html, body { width: 1200px; height: 1023px; overflow: hidden; }
  body {
    background: var(--stage);
    font-family: "Roboto Condensed", Arial, sans-serif;
    position: relative;
  }
  .card {
    position: absolute;
    width: 540px;
    height: 340px;
    border-radius: 18px;
    background: linear-gradient(135deg, var(--card) 0%, var(--card-sheen) 45%, var(--card) 75%);
    box-shadow: 0 18px 40px rgba(0,0,0,.45);
    overflow: hidden;
  }
  .card-front { left: 60px; top: 110px; }
  .card-back { left: 600px; top: 573px; }

  .brand {
    position: absolute;
    left: 44px;
    bottom: 56px;
    display: flex;
    align-items: center;
    gap: 14px;
  }
  .brand-square {
    width: 40px;
    height: 40px;
    background: var(--silver);
  }
  .brand-name {
    font-size: 58px;
    font-weight: 500;
    line-height: 1;
    letter-spacing: 1px;
    color: var(--silver);
  }

  .contact {
    position: absolute;
    left: 300px;
    top: 62px;
    color: var(--silver);
  }
  .contact-name {
    font-size: 27px;
    font-weight: 500;
    color: var(--name);
    letter-spacing: .5px;
  }
  .contact-role {
    font-size: 14px;
    letter-spacing: 1px;
    color: var(--silver-mid);
    margin-bottom: 18px;
  }
  .contact-line {
    font-size: 17px;
    line-height: 1.45;
    display: flex;
    align-items: center;
    gap: 8px;
    color: var(--silver);
  }
  .contact-line.address { color: var(--silver-mid); }
  .contact-line.gap { margin-top: 12px; }
  .icon { width: 13px; height: 13px; flex: none; }
</style>
</head>
<body>
  <section class="card card-front">
    <div class="brand">
      <span class="brand-square"></span>
      <span class="brand-name">KVTL</span>
    </div>
  </section>

  <section class="card card-back">
    <div class="contact">
      <div class="contact-name">JONAS KELLER</div>
      <div class="contact-role">DIRECTOR</div>
      <div class="contact-line address">Kellberger Str. 18</div>
      <div class="contact-line address">71586 Kellbach</div>
      <div class="contact-line gap">
        <svg class="icon" viewBox="0 0 16 16" aria-hidden="true"><path d="M4 1.5 6.5 4 5 6c.9 1.9 2.9 3.9 5 5l2-1.5 2.5 2.5-2 2.5C7 14 2 9 1.5 3.5z" fill="#aaaaaa"/></svg>
        07146-839214-0
      </div>
      <div class="contact-line">
        <svg class="icon" viewBox="0 0 16 16" aria-hidden="true"><rect x="1" y="3" width="14" height="10" rx="1" fill="none" stroke="#aaaaaa" stroke-width="1.5"/><path d="M1.5 4 8 9l6.5-5" fill="none" stroke="#aaaaaa" stroke-width="1.5"/></svg>
        Name@agentur-kvtl.de
      </div>
    </div>
  </section>
</body>
</html>
```